Uncoded front page web design for wedding and event planning company

Hi.

I am launching a wedding and event planning company called Silver Fern Celebrations and need a professional and appealing web design.

So, let me explain my company. I am based in Swindon in Wiltshire but the company will plan weddings and events in Oxfordshire, Wiltshire, Berkshire and London.

We will plan weddings, birthdays, conferences, product launches, fashion shows and conventions but the main focus of the website at this stage should be the weddings with all the other occasions being covered under a single 'events' heading.

My contact details for the website should be:
Maureen Hollis
maureen@silverferncelebrations.co.uk
01793 587203 / 07781 452638

I'd like the website to feel clean, bright and elegant and be set against a white or off-white background. My logo is purple and I'd therefore like some purple incorporated into the design although feel free to use a more muted purple as my one might be a little bright? I'm also considering whether it would look nice paired with a little of the colour gold - maybe as a font colour in places?? I'll leave you to figure that one out as your design eye will be better than mine but for your reference below is my purple colour and my suggested gold one....

My purple colour is Pantone 2592 C but feel free to use others
My suggested gold I'm looking at is Pantone 14-1041 TCX

I would like to incorporate a Facebook feed in the front page if possible, if it looks right. I'd also like to include a variety of pictures as well so I've included a few in a Dropbox folder which is linked below. Please don't feel obliged to use them all by any means (there's loads!) but you've got a few there to play with. If you find any other royalty free images you'd rather use please go ahead but on the understanding I can have them afterwards!

My logo can be retrieved via this Dropbox link...
You'll notice there are 2 styles of placement. Please feel free to use either to fit in with your design...
https://www.filevault.example/sh/kq8pw2mzr4tn7ab/BBBQrt6hNxyvpe5L81GmsWd3Pc?dl=0

The wedding images I have are in this Dropbox folder...
https://www.filevault.example/sh/m9vc2xh6pl1qw8j/BBB4zkrNvLpte6P57YhaJoscb?dl=0

Other than that, it's over to you.... I can't wait to receive your designs :-)

Ooh....finally just to say, as I receive designs in I think I'll notice aspects that I like and don't like and if I feel they'll be useful for other designers, I'll update my brief below. Thanks

BRIEF UPDATE:
Someone asked if I had a tag-line. Could you use "Creating exquisite occasions today for amazing memories tomorrow"

I realise I hadn't explained what I'd like included on my home page so here's some notes to consider....

A welcome to section for me to start narrative about us and our services which has a button that links to our 'about us' page and 'services' page for further information.

A section that nicely illustrates what services we offer whether that be with icons or pictures.

A section with some photos in that would link to our gallery

A section that shows some customer reviews and blog entries that would link to my reviews page and blog to read more.

And finally a contact us section with my details, social media links and site map.

***
I also need to draw attention to where in the UK my services cover. I was therefore thinking perhaps we could use a picture to demonstrate this where it highlights Wiltshire, Oxfordshire, Berkshire and London on a map thereby demonstrating our areas covered. I have found several English county maps when searching on Google but I'm not sure how to highlight the areas I cover (or dull out the areas I don't) so if you have any ideas on this, I'd really like it incorporated. Thanks. (by the way, for those of you not familiar with English counties, the ones I cover are often abbreviated to Wilts, Oxon, Berks, London, so if you find a suitable map with those names on rather than the full names, you'll know what they are!)

I've found an image of the county map which might work well. I was wondering whether we might somehow grey out the counties I don't cover and just keep the ones I do as mentioned above and then crop it into perhaps a shadowed circle? I've attached a screenshot to the brief.

I've decided on the tag-line "Creating exquisite occasions today for amazing memories tomorrow" so if that could be included somewhere that would be great. I also need to draw attention to where in the UK my services cover. I was therefore thinking perhaps we could use a picture to demonstrate this where it highlights Wiltshire, Oxfordshire, Berkshire and London on a map thereby demonstrating our areas covered. I have found several English county maps when searching on Google but I'm not sure how to highlight the areas I cover (or dull out the areas I don't) so if you have any ideas on this, I'd really like it incorporated. Thanks. Added Wednesday, June 24, 2015

Target Market(s)

Predominately women aged 25-55

Industry/Entity Type

Wedding Planner

Number of Pages Required

1 page

Font styles to use
Sans Serif
Script

Requirements
Nice to have
• I'd like to see how the colour theme of purple and perhaps a little gold (maybe as a font colour) look against a white background. I've mentioned the Pantone colours in the brief above.
• I've attached a screenshot of a webpage with gold writing in and fonts that I like. Perhaps it could give you inspiration?
Should not have
• I really don't like the font SCRIPTINA so please done use that.

```html
<!DOCTYPE html>
<html lang="en">
<head>
<meta charset="utf-8">
<title>Silver Fern Celebrations – Find Us</title>
<link rel="stylesheet" href="https://fonts.googleapis.com/css2?family=Lato:wght@300;400&family=Roboto:wght@400;500&display=swap">
<style>
  :root {
    --plum: #912c8c;
    --plum-card: #952f8e;
    --band-light: #c0509f;
    --band-mid: #a33b93;
    --band-deep: #7d1f7a;
    --map-base: #efe4e5;
    --map-warm: #e6cfd1;
    --white: #ffffff;
    --soft-white: rgba(255,255,255,0.62);
    --footer-bg: #292929;
    --footer-text: #d2d2d2;
    --button-bg: #ececec;
    --button-line: #9a9a9a;
  }
  * { margin: 0; padding: 0; box-sizing: border-box; }
  html, body { width: 1200px; height: 895px; overflow: hidden; background: var(--white); }
  body { font-family: "Roboto", Arial, sans-serif; position: relative; }

  .find-us { position: absolute; top: 0; left: 0; width: 1200px; height: 98px; }
  .find-us__title {
    position: absolute; top: 16px; width: 100%; text-align: center;
    font-family: "Lato", Arial, sans-serif; font-weight: 300; font-size: 37px;
    letter-spacing: 1px; color: var(--plum);
  }

  .map-area {
    position: absolute; top: 98px; left: 0; width: 1200px; height: 349px;
    background: radial-gradient(ellipse at 45% 55%, var(--map-warm) 0%, var(--map-base) 70%);
  }

  .office-card {
    position: absolute; top: 147px; left: 889px; width: 230px; height: 151px;
    background: var(--plum-card); color: var(--white);
  }
  .office-card__pointer { position: absolute; left: 0; top: 150px; }
  .office-card__title {
    position: absolute; top: 21px; left: 23px;
    font-family: "Lato", Arial, sans-serif; font-weight: 300; font-size: 24px;
  }
  .office-card__pin { position: absolute; top: 69px; left: 30px; }
  .office-card__address {
    position: absolute; top: 71px; left: 67px;
    font-size: 11.5px; font-weight: 500; line-height: 15px;
  }

  .values-band {
    position: absolute; top: 447px; left: 0; width: 1200px; height: 382px;
    background:
      linear-gradient(115deg, var(--band-light) 0%, var(--band-mid) 38%, rgba(125,31,122,0.0) 60%),
      linear-gradient(160deg, var(--band-mid) 0%, var(--band-deep) 100%);
  }
  .brand {
    position: absolute; top: 100px; left: 80px; width: 300px; text-align: center;
    color: var(--white);
  }
  .brand__mark {
    width: 96px; height: 96px; margin: 0 auto 28px;
    border: 2px solid var(--white); border-radius: 50%;
  }
  .brand__name {
    font-family: "Lato", Arial, sans-serif; font-weight: 300; font-size: 34px;
    line-height: 38px; letter-spacing: 1px;
  }

  .value { position: absolute; top: 96px; width: 330px; color: var(--white); }
  .value--team { left: 429px; }
  .value--personal { left: 784px; }
  .value__title {
    font-family: "Lato", Arial, sans-serif; font-weight: 300; font-size: 23px;
    text-transform: uppercase; margin-bottom: 18px;
  }
  .value__lead { font-size: 13px; line-height: 23px; margin-bottom: 22px; }
  .value__text { font-size: 13px; line-height: 23px; color: var(--soft-white); }

  .site-footer {
    position: absolute; top: 829px; left: 0; width: 1200px; height: 66px;
    background: var(--footer-bg);
  }
  .site-footer__copy {
    position: absolute; top: 31px; left: 74px;
    font-size: 11.5px; color: var(--footer-text);
  }
  .back-to-top {
    position: absolute; top: 20px; left: 1079px; width: 39px; height: 37px;
    background: var(--button-bg); border-radius: 2px;
    display: flex; align-items: center; justify-content: center;
  }
</style>
</head>
<body>
  <section class="find-us">
    <h2 class="find-us__title">FIND US</h2>
  </section>

  <div class="map-area" role="img" aria-label="Road map of southern England from Bristol to London showing the areas covered"></div>

  <aside class="office-card">
    <h3 class="office-card__title">Our office</h3>
    <svg class="office-card__pin" width="12" height="17" viewBox="0 0 12 17" aria-hidden="true">
      <path d="M6 0C2.7 0 0 2.6 0 5.9 0 10.2 6 17 6 17s6-6.8 6-11.1C12 2.6 9.3 0 6 0z" fill="#4a0f45"/>
      <circle cx="6" cy="6" r="2.2" fill="#952f8e"/>
    </svg>
    <p class="office-card__address">Silver Fern<br>Wiltshire, Oxfordshire,<br>Berkshire and London</p>
    <svg class="office-card__pointer" width="30" height="28" viewBox="0 0 30 28" aria-hidden="true">
      <polygon points="0,0 30,0 0,28" fill="#952f8e"/>
    </svg>
  </aside>

  <section class="values-band">
    <div class="brand">
      <div class="brand__mark"></div>
      <p class="brand__name">Silver Fern<br>Celebrations</p>
    </div>

    <article class="value value--team">
      <h3 class="value__title">Team integrity</h3>
      <p class="value__lead">Vestibulum commodo volutpat a, convallis ac, laoreet enim. Phasellus fermentum in, dolor pellentesque.</p>
      <p class="value__text">Mulla imperdiet sit amet magna. Vestibulum dapibus, mauris nec malesuada fames ac turpis velit, rhoncus eu, luctus et interdum adipiscing wisi.</p>
    </article>

    <article class="value value--personal">
      <h3 class="value__title">Personal integrity</h3>
      <p class="value__lead">Quisque lorem tortor fringilla sed, vestibulum id, eleifend justo vel bibendum massa ac turpis faucibus</p>
      <p class="value__text">In hendrerit nulla quam nunc, accumsan congue. Lorem ipsum primis in nibh vel risus. Sed vel lectus. Ut sagittis, ipsum dolor quam.</p>
    </article>
  </section>

  <footer class="site-footer">
    <p class="site-footer__copy">© 2015 Silver Fern Celebrations. All Rights Reserved.</p>
    <div class="back-to-top" aria-label="Back to top">
      <svg width="12" height="7" viewBox="0 0 12 7" aria-hidden="true">
        <polyline points="1,6 6,1 11,6" fill="none" stroke="#9a9a9a" stroke-width="1.2"/>
      </svg>
    </div>
  </footer>
</body>
</html>
```